4th Generation Family Business Needs a New Card Design!

We are a family owned 4th Generation company. We are based in the Sydney, Australia area and we are desperately in need of a more modern and classy card. We are monumental masons who design, supply & erect lasting memorials throughout cemeteries in Sydney. Our customers are normally in a period of grieving. I have attached logo files that will need to be implemented on the card. Company was established 1935. Australian Owned and Operated. Card needs to be designed to PIXO.com specification.

Target Market(s)

Our target market is based upon people that a grieving for family members that have passed away. We also deal with alot of companies that own and operate cemeteries.

Industry/Entity Type

Business

Contact Information for Business Card

Simon Harcourt, Operations Manager, 0417293086, simon@harcourtmemorials.com.au
Lewis Harcourt, Director, 0491630572, lewis@harcourtmemorials.com.au
Phone # 02 9561 3048
Website: www.harcourtmemorials.com.au
Address: Suite 17, 8 Palfrey Lane, West Carlow, Sydney NSW 2156

Font styles to use
Serif
Decorative
Script

Requirements
Must have
• Would like to see the logo nicely implemented with a modern design. Embossed lettering would be a nice additive.

```html
<!DOCTYPE html>
<html lang="en">
<head>
<meta charset="utf-8">
<title>Harcourt Memorials – Business Card</title>
<link rel="stylesheet" href="https://fonts.googleapis.com/css2?family=Open+Sans:wght@400;600;700&display=swap">
<style>
  :root {
    --stage: #e9e6e1;
    --card-dark: #232323;
    --card-light: #ffffff;
    --gold: #f2c21b;
    --ink-light: #f4f4f4;
    --ink-dark: #1e1e1e;
  }
  * { box-sizing: border-box; margin: 0; padding: 0; }
  html, body {
    width: 1200px; height: 950px; overflow: hidden;
    background: var(--stage);
    font-family: "Open Sans", Arial, sans-serif;
  }
  .stage {
    position: relative; width: 1200px; height: 950px;
    display: flex; justify-content: center; align-items: center; gap: 80px;
  }
  .card {
    position: relative; width: 390px; height: 650px;
    box-shadow: 0 10px 30px rgba(0,0,0,.18);
  }
  .card--front { background: var(--card-dark); color: var(--ink-light); }
  .card--back { background: var(--card-light); color: var(--ink-dark);
    display: flex; align-items: center; justify-content: center; }
  .card__frame { position: absolute; inset: 0; }
  .card__content {
    position: absolute; inset: 0;
    display: flex; flex-direction: column; align-items: center;
    text-align: center; padding-top: 62px;
  }
  .brand {
    display: flex; flex-direction: column; align-items: center;
    font-weight: 600; line-height: 1.1; letter-spacing: 4px;
  }
  .brand__name { font-size: 40px; }
  .brand__sub { font-size: 16px; letter-spacing: 8px; margin-top: 6px; }
  .card--front .brand { color: var(--ink-light); }
  .card--back .brand { color: var(--ink-dark); }
  .card--back .brand__name { font-size: 46px; }
  .card--back .brand__sub { font-size: 18px; }
  .contact__icon { display: block; margin: 0 auto 4px; }
  .person { margin-top: 58px; }
  .person__name {
    color: var(--gold); font-weight: 700; font-size: 21px; letter-spacing: 1px;
  }
  .person__role { font-size: 15px; letter-spacing: 1.5px; margin-top: 2px; }
  .contact { list-style: none; margin-top: 20px; font-size: 15px; line-height: 1.35; }
  .contact li { margin-bottom: 13px; }
</style>
</head>
<body>
<main class="stage">

  <section class="card card--front" aria-label="Business card front">
    <svg class="card__frame" width="390" height="650" viewBox="0 0 390 650">
      <path d="M48 18 H342 V34 H372 V616 H342 V632 H48 V616 H18 V34 H48 Z"
            fill="none" stroke="var(--gold)" stroke-width="6"/>
    </svg>
    <div class="card__content">
      <div class="brand">
        <span class="brand__name">HARCOURT</span>
        <span class="brand__sub">MEMORIALS</span>
      </div>

      <div class="person">
        <svg class="contact__icon" width="16" height="16" viewBox="0 0 16 16" fill="var(--gold)">
          <circle cx="8" cy="5" r="3.5"/><path d="M1 16 C1 10 15 10 15 16 Z"/>
        </svg>
        <p class="person__name">SIMON HARCOURT</p>
        <p class="person__role">OPERATIONS MANAGER</p>
      </div>

      <ul class="contact">
        <li>
          <svg class="contact__icon" width="14" height="18" viewBox="0 0 14 18" fill="var(--gold)">
            <path d="M7 0 C3 0 0 3 0 7 C0 12 7 18 7 18 C7 18 14 12 14 7 C14 3 11 0 7 0 Z M7 4 A3 3 0 1 1 7 10 A3 3 0 1 1 7 4 Z"/>
          </svg>
          Suite 17, 8 Palfrey Lane<br>West Carlow, Sydney NSW 2156
        </li>
        <li>
          <svg class="contact__icon" width="18" height="14" viewBox="0 0 18 14" fill="var(--gold)">
            <path d="M1 4 C1 1 17 1 17 4 V6 H13 V4 H5 V6 H1 Z"/><rect x="3" y="7" width="12" height="7" rx="1"/>
          </svg>
          02 9561 3048
        </li>
        <li>
          <svg class="contact__icon" width="10" height="16" viewBox="0 0 10 16" fill="var(--gold)">
            <rect x="0" y="0" width="10" height="16" rx="2"/><rect x="2" y="2" width="6" height="10" fill="var(--card-dark)"/>
          </svg>
          0417293086
        </li>
        <li>
          <svg class="contact__icon" width="18" height="12" viewBox="0 0 18 12" fill="var(--gold)">
            <rect width="18" height="12" rx="1"/><path d="M1 1 L9 7 L17 1" fill="none" stroke="var(--card-dark)" stroke-width="1.5"/>
          </svg>
          simon@harcourtmemorials.com.au
        </li>
        <li>
          <svg class="contact__icon" width="16" height="16" viewBox="0 0 16 16" fill="none" stroke="var(--gold)" stroke-width="1.5">
            <circle cx="8" cy="8" r="7"/><ellipse cx="8" cy="8" rx="3" ry="7"/><path d="M1 8 H15"/>
          </svg>
          www.harcourtmemorials.com.au
        </li>
      </ul>
    </div>
  </section>

  <section class="card card--back" aria-label="Business card back">
    <div class="brand">
      <span class="brand__name">HARCOURT</span>
      <span class="brand__sub">MEMORIALS</span>
    </div>
  </section>

</main>
</body>
</html>
```